"HTML Email Template"

We are wanting to get a html template built for the purpose of a monthly email that we send out to our database. Currently we send them out in an email form and looking to bring some more colour and graphics to jazz it up a little.
Our webpage address is www.bluelanternpartners.com.au
It targets people in the innovation, development, strategy, collaboration and entrepreneurship space.
The monthly email contains an into paragraph and up to about ten items with links to articles etc
We would like to stick with a similar colour scheme as seen on our webpage.
The final design should look professional and edgy
Updates

Hi

We have just changed this status of this project to Guaranteed Payment
Looking forward to start receiving some great designs
Thanks

Target Market(s)

Senior executives in corporations, professionals

Industry/Entity Type

It Professional

```html
<!DOCTYPE html>
<html lang="en">
<head>
<meta charset="utf-8">
<title>Blue Lantern Partners – Monthly Newsletter</title>
<link rel="stylesheet" href="https://fonts.googleapis.com/css2?family=Arimo:wght@400;700&display=swap">
<style>
  :root {
    --header-bg: #c7d0ce;
    --header-line: #aab4b2;
    --page-bg: #f1f1f0;
    --card-bg: #ffffff;
    --frame: #dcdcdc;
    --brand-blue: #2f7fbf;
    --accent: #7ccbea;
    --accent-dark: #3fa6d2;
    --date-text: #2e6d8e;
    --heading: #444444;
    --title: #1e1e1e;
    --body-text: #a3a3a3;
    --divider: #dddddd;
  }
  * { box-sizing: border-box; margin: 0; padding: 0; }
  html, body {
    width: 900px; height: 1200px; overflow: hidden;
    background: var(--page-bg);
    font-family: "Arimo", Helvetica, Arial, sans-serif;
  }
  .canvas { position: relative; width: 900px; height: 1200px; overflow: hidden; }

  /* Header */
  .masthead {
    position: absolute; left: 0; top: 0; width: 900px; height: 83px;
    background: var(--header-bg);
    border-bottom: 1px solid var(--header-line);
  }
  .brand {
    position: absolute; left: 125px; top: 24px;
    display: flex; align-items: center; gap: 10px;
  }
  .brand-dot { width: 30px; height: 30px; border-radius: 50%; background: var(--brand-blue); }
  .brand-name { font-size: 26px; font-weight: 700; color: var(--brand-blue); letter-spacing: -0.5px; }
  .social { position: absolute; top: 11px; right: 124px; display: flex; gap: 9px; }
  .social-btn {
    width: 31px; height: 31px; border-radius: 50%;
    background: #e6eceb; border: 1px solid #9fa9a7;
  }
  .issue-date {
    position: absolute; right: 125px; top: 49px;
    display: flex; align-items: center; gap: 14px;
    font-size: 17px; color: #2a2a2a;
  }

  /* Intro */
  .intro { position: absolute; left: 125px; top: 105px; width: 390px; }
  .intro-heading { font-size: 17px; line-height: 23px; color: var(--heading); font-weight: 400; }
  .intro-body { margin-top: 6px; font-size: 14px; line-height: 20px; color: var(--body-text); }
  .btn {
    display: inline-block; text-align: center; color: #23536b;
    background: linear-gradient(#b4e6f8, #6cc6ea);
    border: 1px solid var(--accent-dark); border-radius: 3px;
    box-shadow: 0 2px 0 #6a8e9c;
    text-decoration: none;
  }
  .btn-visit { position: absolute; left: 0; top: 209px; width: 80px; height: 29px; line-height: 27px; font-size: 13px; }
  .portrait {
    position: absolute; left: 537px; top: 107px; width: 236px; height: 236px;
    border-radius: 50%; border: 3px solid var(--accent);
    background: radial-gradient(circle at 50% 40%, #c9a28e 0%, #8a6a5c 45%, #3e3b3c 100%);
  }

  /* Posts */
  .posts-frame {
    position: absolute; left: 117px; top: 385px; width: 666px; height: 830px;
    border: 1px solid var(--frame); background: #f6f6f6;
  }
  .posts {
    position: absolute; left: 6px; top: 8px; width: 652px; height: 830px;
    background: var(--card-bg); border: 1px solid var(--frame);
    padding: 0 16px;
  }
  .post-row {
    display: flex; justify-content: space-between;
    height: 179px; padding-top: 13px;
    border-bottom: 2px solid var(--divider);
  }
  .post { width: 302px; }
  .post-head { display: flex; gap: 7px; min-height: 44px; }
  .date-badge {
    flex: none; width: 36px; height: 36px; background: var(--accent);
    text-align: center; color: var(--date-text);
  }
  .date-day { display: block; font-size: 18px; font-weight: 700; line-height: 20px; padding-top: 2px; }
  .date-month { display: block; font-size: 11px; line-height: 12px; }
  .post-title { font-size: 15px; line-height: 22px; color: var(--title); font-weight: 400; margin-top: -3px; }
  .post-excerpt { margin-top: 3px; font-size: 12px; line-height: 18px; color: var(--body-text); }
  .btn-read { margin-top: 14px; width: 82px; height: 22px; line-height: 20px; font-size: 11.5px; }
</style>
</head>
<body>
<div class="canvas">
  <header class="masthead">
    <div class="brand"><span class="brand-dot"></span><span class="brand-name">Blue Lantern Partners</span></div>
    <div class="social"><span class="social-btn"></span><span class="social-btn"></span></div>
    <div class="issue-date">
      <svg width="22" height="15" viewBox="0 0 22 15" aria-hidden="true"><rect x="0.5" y="0.5" width="21" height="14" fill="#f4f6f6" stroke="#fff"/><path d="M1 1 L11 9 L21 1" fill="none" stroke="#c9d0cf" stroke-width="1.2"/></svg>
      <span>20 December 2012</span>
    </div>
  </header>

  <section class="intro">
    <h1 class="intro-heading">BlueLantern’s monthly newsletter.<br>Check the latest news from us.</h1>
    <p class="intro-body">Blue Lantern Partners delivers real value in the areas of strategy, innovation, collaboration and globalisation, underpinned by technology.<br>We look to provide business impact to you and to all our clients. The Blue Lantern team has years of business xperience in hands-on commercial roles, and as such can eliver exceptional value and outcomes.</p>
    <a class="btn btn-visit" href="#">Visit us!</a>
  </section>
  <div class="portrait" role="img" aria-label="Portrait photo of the firm's director"></div>

  <div class="posts-frame">
    <main class="posts">
      <div class="post-row">
        <article class="post"><div class="post-head"><div class="date-badge"><span class="date-day">01</span><span class="date-month">FEB</span></div><h2 class="post-title">The post title is longer than before. Also provide in 2 lines.</h2></div><p class="post-excerpt">Sed ut perspiciatis unde omnis iste natus error sitt-voluptatem accusantium doloremque laudantium, totam rem aperiam, eaque ipsa quae ab illoo invento.</p><a class="btn btn-read" href="#">Read more</a></article>
        <article class="post"><div class="post-head"><div class="date-badge"><span class="date-day">01</span><span class="date-month">FEB</span></div><h2 class="post-title">The post title is longer than before. A lot of variations here.</h2></div><p class="post-excerpt">Sed ut perspiciatis unde omnis iste natus error sitt-voluptatem accusantium doloremque laudantium, totam rem aperiam, eaque ipsa quae ab illoo invento.</p><a class="btn btn-read" href="#">Read more</a></article>
      </div>
      <div class="post-row">
        <article class="post"><div class="post-head"><div class="date-badge"><span class="date-day">15</span><span class="date-month">FEB</span></div><h2 class="post-title">The post title is longer than before. Also provide in 2 lines.</h2></div><p class="post-excerpt">Sed ut perspiciatis unde omnis iste natus error sitt-voluptatem accusantium doloremque laudantium, totam rem aperiam, eaque ipsa quae ab illoo invento.</p><a class="btn btn-read" href="#">Read more</a></article>
        <article class="post"><div class="post-head"><div class="date-badge"><span class="date-day">21</span><span class="date-month">FEB</span></div><h2 class="post-title">The post title also can be the short.</h2></div><p class="post-excerpt">Sed ut perspiciatis unde omnis iste natus error sitt-voluptatem accusantium doloremque laudantium, totam rem aperiam, eaque ipsa quae ab illoo invento.</p><a class="btn btn-read" href="#">Read more</a></article>
      </div>
      <div class="post-row">
        <article class="post"><div class="post-head"><div class="date-badge"><span class="date-day">22</span><span class="date-month">FEB</span></div><h2 class="post-title">The post title is longer than before. You can change the date &amp; month.</h2></div><p class="post-excerpt">Sed ut perspiciatis unde omnis iste natus error sitt-voluptatem accusantium doloremque laudantium, totam rem aperiam, eaque ipsa quae ab illoo invento.</p><a class="btn btn-read" href="#">Read more</a></article>
        <article class="post"><div class="post-head"><div class="date-badge"><span class="date-day">14</span><span class="date-month">JUN</span></div><h2 class="post-title">The post title is longer than before. A lot of variations here.</h2></div><p class="post-excerpt">Sed ut perspiciatis unde omnis iste natus error sitt-voluptatem accusantium doloremque laudantium, totam rem aperiam, eaque ipsa quae ab illoo invento.</p><a class="btn btn-read" href="#">Read more</a></article>
      </div>
      <div class="post-row">
        <article class="post"><div class="post-head"><div class="date-badge"><span class="date-day">20</span><span class="date-month">JUN</span></div><h2 class="post-title">Only 1 line for this title.</h2></div><p class="post-excerpt">Sed ut perspiciatis unde omnis iste natus error sitt-voluptatem accusantium doloremque laudantium, totam rem aperiam, eaque ipsa quae ab illoo invento.</p><a class="btn btn-read" href="#">Read more</a></article>
        <article class="post"><div class="post-head"><div class="date-badge"><span class="date-day">31</span><span class="date-month">AUG</span></div><h2 class="post-title">The post title is longer than before. This post is linked.</h2></div><p class="post-excerpt">Sed ut perspiciatis unde omnis iste natus error sitt-voluptatem accusantium doloremque laudantium, totam rem aperiam, eaque ipsa quae ab illoo invento.</p><a class="btn btn-read" href="#">Read more</a></article>
      </div>
      <div class="post-row">
        <article class="post"><div class="post-head"><div class="date-badge"><span class="date-day">01</span><span class="date-month">FEB</span></div><h2 class="post-title">The post title is longer than before. Also provide in 2 lines.</h2></div><p class="post-excerpt">Sed ut perspiciatis unde omnis iste natus error sitt-voluptatem accusantium doloremque laudantium, totam rem aperiam, eaque ipsa quae ab illoo invento.</p><a class="btn btn-read" href="#">Read more</a></article>
        <article class="post"><div class="post-head"><div class="date-badge"><span class="date-day">01</span><span class="date-month">FEB</span></div><h2 class="post-title">The post title is longer than before. A lot of variations here.</h2></div><p class="post-excerpt">Sed ut perspiciatis unde omnis iste natus error sitt-voluptatem accusantium doloremque laudantium, totam rem aperiam, eaque ipsa quae ab illoo invento.</p><a class="btn btn-read" href="#">Read more</a></article>
      </div>
    </main>
  </div>
</div>
</body>
</html>
```